E-Book-Cover für einen Kriminalroman
Zielgruppe
Ich veröffentliche meinen Roman “Die Schwelle” als E-Book.
Das Buch spielt in einer nahen Zukunft, in der Die Schwelle Nachrichten in die Vergangenheit möglich macht. Unfälle und Straftaten werden sofort ungeschehen gemacht. Jeder Bürger kann seinem vergangenen Ich eine Botschaft schicken - und so die eigene Geschichte “reparieren”. Auch Henrik, ein unscheinbarer Projektleiter, erhält eines Tag eine Nachricht aus der Zukunft: 'Halte dich von Maren fern. Sie wird dein Untergang sein'. Die Nachricht stellt Henrik vor ein Rätsel. Vor welcher Gefahr hat er sich gewarnt? Und wer ist Maren? Ein Jahr später wird Henrik durch Zufall Mitwisser einer politischen Verschwörung. Die Killer machen Jagd auf ihn und kennen jeden seiner nächsten Schritte. Die letzte Rettung ist ausgerechnet eine Frau namens Maren.
--- “Die Schwelle” spielt in der Zukunft, ist aber kein Science Fiction Roman. Die beschriebene Welt ist (außer der Zeitmanipulation) wie die unsere. Am ehesten ist das Buch also ein actionreicher Kriminalroman.
Die Hauptzielgruppe sind 25 - 45-jährige, zum Beispiel Leser von Rolf Ebenhöch, Tobias Wendrath oder Karl Vossberg.
Aufgabenstellung
Gewünscht ist ein E-Book-Cover für die Verwendung auf Online-Plattformen wie Kaufora.
Autor: K.J. Brandau
Titel: Die Schwelle
Zusatz: Roman
Visuelle Anforderungen
Das Cover sollte eine Reihe von Türen zeigen. Begründung dazu: Im sogenannten Registerbüro muss der Protagonist in einer von vier nebeneinanderliegenden Türen treten und empfängt dort seine Nachricht aus der Zukunft. Das Thema “Entscheidungen fürs Leben” des Romans wird durch diese Türen visualisiert und als Symbol mehrmals aufgegriffen - dementsprechend ist es aus meiner Sicht perfekt für das Cover.
Für die Fotosuche: Das Registerbüro ist leicht heruntergekommen und wirkt kühl und unsympathisch. Dieses Bild https://de.bildquelle-beispiel.de/id/19384726 (auch noch einmal angehängt) zum Beispiel passt sehr gut.
Thema Hacking und Programmieren
Das Buch spielt in den Lebenswelten von Programmierern und Hackern; Die Schwelle ist eine Datenbank. Dies könnte durch Stil der Schrift oder anders unterstützt werden. Nur, wenn sinnvoll und ohne dass es wie ein Computerbuch aus den 90ern wirkt natürlich :)
- Die Font kann das Thema aufgreifen, aber bitte KEINE Vintage LED-Schrift im Stil von http://www.schriftkiste-beispiel.de/segment-alt.font, sondern eine die einem modernen Monitor entspringt. Entweder verpixelt (Beispiel im Anhang) oder durch eine gepunktete Schrift in hoher "Auflösung" (Beispiel: http://www.schriftkiste-beispiel.de/perlen-raster.font, also nicht nur 7 Punkte in der Breite), hier könnte man die Ränder auch etwas blurren, um den Effekt eines Monitors zu erzielen
- Wenn der o.g. Schriftstil benutzt wird, bitte in Kleinbuchstaben (wie ein Befehl auf dem Terminal)
-> All kein Muss, nur wenn sinnvoll!
Weitere Anforderungen:
- Die Türen befinden sich in einem kühlen, sterilen BÜRO, dementsprechend dürfen sie nicht zu hübsch aussehen oder an Wohnzimmertüren erinnern
- Wenn Codezeilen als Hintergrundbestandteil genutzt..

```html
<!DOCTYPE html>
<html lang="de">
<head>
<meta charset="utf-8">
<title>Die Schwelle – K.J. Brandau</title>
<link rel="stylesheet" href="https://fonts.googleapis.com/css2?family=Amatic+SC:wght@400;700&display=swap">
<style>
  :root {
    --stage: #c9c9c9;
    --stage-light: #dedede;
    --wall-top: #262626;
    --wall-mid: #2e2e2e;
    --wall-haze: #5a5a5a;
    --floor: #2a2a2a;
    --ink: #f4f4f4;
    --echo: rgba(150, 150, 150, 0.6);
    --door-wood: #6b3d24;
    --door-dark: #3f2416;
    --door-frame: #bdbdbd;
  }
  * { margin: 0; padding: 0; box-sizing: border-box; }
  html, body { width: 1200px; height: 800px; overflow: hidden; }
  body {
    background: radial-gradient(ellipse at 50% 40%, var(--stage-light), var(--stage));
    display: flex;
    align-items: center;
    justify-content: center;
    font-family: "Amatic SC", cursive;
  }
  .cover {
    position: relative;
    width: 475px;
    height: 760px;
    overflow: hidden;
    background:
      radial-gradient(ellipse 70% 18% at 70% 58%, rgba(120,120,120,0.35), transparent 70%),
      linear-gradient(180deg, var(--wall-top) 0%, var(--wall-mid) 55%, #3a3a3a 68%, var(--floor) 100%);
    color: var(--ink);
    text-align: center;
  }
  .cover__author, .cover__article, .cover__title, .cover__genre {
    position: absolute;
    left: 0;
    right: 0;
    font-weight: 700;
    line-height: 1;
    text-shadow: 4px 10px 0 var(--echo);
  }
  .cover__author { top: 48px; font-size: 84px; letter-spacing: 1px; }
  .cover__article { top: 158px; font-size: 118px; }
  .cover__title { top: 258px; font-size: 172px; letter-spacing: -2px; text-shadow: 6px 14px 0 var(--echo); }
  .cover__genre { top: 455px; font-size: 52px; text-shadow: 2px 6px 0 var(--echo); }
  .cover__doors {
    position: absolute;
    left: 48px;
    top: 582px;
    width: 384px;
    height: 170px;
  }
</style>
</head>
<body>
  <main class="cover">
    <p class="cover__author">K.J. Brandau</p>
    <h1>
      <span class="cover__article">Die</span>
      <span class="cover__title">Schwelle</span>
    </h1>
    <p class="cover__genre">Roman</p>
    <svg class="cover__doors" viewBox="0 0 384 170" role="img" aria-label="Foto: vier nummerierte Bürotüren nebeneinander an einer kahlen Betonwand, die zweite Tür steht einen Spalt offen, darüber rote und grüne Signallampen">
      <defs>
        <linearGradient id="doorTone" x1="0" y1="0" x2="0" y2="1">
          <stop offset="0" stop-color="var(--door-dark)"/>
          <stop offset="0.5" stop-color="var(--door-wood)"/>
          <stop offset="1" stop-color="var(--door-dark)"/>
        </linearGradient>
      </defs>
      <rect x="0" y="0" width="384" height="170" fill="url(#doorTone)" opacity="0.85"/>
    </svg>
  </main>
</body>
</html>
```